Black Granite Web Design Project

We are looking for a design for a new company that will be selling Black Granite slabs and tiles. We will be selling to both end-consumers and granite installers. We have already settled on a logo and hopefully this will give an idea of what we like in our designs. We are not going to be selling online but want people to call us so the site is basically an enhanced business card. We will be focusing a lot on SEO so the design will have to keep that in mind.

We would like to keep the design in 1024x768 to make it easily view-able on all devices.

Regarding navigation there should only be a few sub-pages, like "Granite Slabs", "Granite Tiles", "Delivery", "Contact"

Aside from that we are open to designs. One idea we did have was to personalize the site and have a person there somehow to represent the company, making the user feel there are real people behind this site. This is just an idea and not a must.

The name of the company and site is "Copper Ridge Marmora"

Thanks
Updates

Hello All,

Thanks for the great designs. There are some good looking designs that show beautiful kitchens but this site is made for the granite installers and not the retail consumers. So in order not to to confuse the buyers I would like to keep this as much about the raw products as possible. The raw products being the granite slabs, thereby making it obvious we don't sell granite counter tops. 

This design will really be the identity of this company so it is important we get the right message across on this index page and that this page is as complete as possible.

Again, thanks for all the work being put into this.

Target Market(s)

The target audience is granite installers or companies that would with granite slabs.

Industry/Entity Type

Business

```html
<!DOCTYPE html>
<html lang="en">
<head>
<meta charset="utf-8">
<title>Copper Ridge Marmora</title>
<link rel="stylesheet" href="https://fonts.googleapis.com/css2?family=Source+Sans+3:wght@400;600;700&family=Oswald:wght@500&display=swap">
<style>
:root{
  --green:#2f4d3c;
  --ink:#222;
  --text:#4a4a4a;
  --muted:#888;
  --band:#f1f1f1;
  --footer:#3b3b3b;
  --footer-dark:#2c2c2c;
  --white:#fff;
  --social:#2f7fc1;
}
*{box-sizing:border-box;margin:0;padding:0}
html,body{width:870px;height:1200px;overflow:hidden;background:var(--white)}
body{position:relative;font-family:"Source Sans 3",sans-serif;color:var(--text)}
.abs{position:absolute}
.brand{left:63px;top:40px;width:170px;font-weight:700;font-size:21px;line-height:22px;color:var(--ink);letter-spacing:-.3px}
.search{left:642px;top:27px;width:164px;height:23px;border:1px solid #ccc;border-radius:3px;font-size:10px;font-style:italic;color:#999;padding:4px 5px}
.search svg{position:absolute;right:6px;top:5px}
.nav a{position:absolute;top:77px;font-size:14px;color:var(--green);text-decoration:none;letter-spacing:.2px}
.hero{left:64px;top:118px;width:743px;height:311px;background:linear-gradient(90deg,#c9c2b8 0%,#d8d3cc 35%,#6b4a3a 55%,#8c7b6d 80%,#5e7a9e 92%,#d9dde2 100%)}
.hero-caption{left:93px;top:280px;width:340px;height:120px;background:rgba(90,88,86,.72);padding:16px 18px;color:var(--white)}
.hero-caption h2{font-family:"Oswald",sans-serif;font-weight:500;font-size:23px;line-height:26px;letter-spacing:.3px}
.hero-caption h3{font-weight:400;font-size:16px;margin-top:6px}
.hero-caption p{font-size:11.5px;line-height:18px;margin-top:7px}
.dots{left:760px;top:411px;display:flex;gap:3px}
.dots i{width:6px;height:6px;border-radius:50%;background:#333;border:1px solid #fff}
.dots i:first-child{background:#fff;border-color:#333}
.welcome{left:0;top:448px;width:870px;text-align:center}
.welcome h1{font-size:19px;font-weight:600;color:var(--green)}
.welcome p{width:700px;margin:10px auto 0;font-size:11.5px;line-height:21px;color:var(--text)}
.btn{left:393px;top:531px;width:90px;height:26px;border-radius:3px;background:linear-gradient(#3a3a3a,#111);color:var(--white);font-size:11px;text-align:center;line-height:26px;box-shadow:0 2px 3px rgba(0,0,0,.35)}
.divider{left:63px;top:572px;width:744px;height:8px;background:radial-gradient(ellipse at center top,rgba(0,0,0,.08),transparent 70%)}
.feature{top:592px;width:180px;text-align:center}
.feature .ring{width:104px;height:104px;margin:0 auto;border-radius:50%;background:#f3f3f3;box-shadow:0 1px 4px rgba(0,0,0,.15);display:flex;align-items:center;justify-content:center}
.feature .disc{width:90px;height:90px;border-radius:50%;background:#1e1e1e;display:flex;align-items:center;justify-content:center}
.feature h4{font-size:16px;font-weight:600;color:var(--green);margin-top:6px}
.feature p{font-size:10.5px;line-height:15.5px;letter-spacing:.4px;margin-top:3px;color:#444}
.projects{left:0;top:805px;width:870px;height:201px;background:var(--band)}
.projects h2{position:absolute;left:62px;top:-10px;font-size:18px;font-weight:600;color:var(--green)}
.project{top:26px}
.project .photo{height:101px;border:1px solid #ddd}
.project p{font-size:9.6px;line-height:15px;margin-top:17px;color:#444}
.footer{left:0;top:1006px;width:870px;height:157px;background:var(--footer)}
.col{top:17px;color:var(--white)}
.col h5{font-size:13.5px;font-weight:400;margin-bottom:6px}
.col li{list-style:none;font-size:10px;line-height:21px;color:#eee}
.foot-brand{left:693px;top:100px;width:90px;font-size:10px;font-weight:700;line-height:11px;color:var(--white)}
.bottom{left:0;top:1163px;width:870px;height:37px;background:var(--footer-dark)}
.bottom p{position:absolute;left:69px;top:12px;font-size:10px;color:#eee}
.social{position:absolute;top:8px;width:21px;height:21px;border-radius:50%;background:var(--social)}
</style>
</head>
<body>

<div class="abs brand">Copper Ridge<br>Marmora</div>

<div class="abs search">Search..
  <svg width="10" height="10" viewBox="0 0 10 10"><circle cx="4" cy="4" r="3" fill="none" stroke="#999" stroke-width="1.4"/><line x1="6.2" y1="6.2" x2="9.3" y2="9.3" stroke="#999" stroke-width="1.6"/></svg>
</div>

<nav class="nav">
  <a style="left:405px">HOME</a>
  <a style="left:465px">GRANIT SLABS</a>
  <a style="left:569px">GRANITE TILES</a>
  <a style="left:674px">DELIVERY</a>
  <a style="left:752px">CONTACT</a>
</nav>

<div class="abs hero" role="img" aria-label="Bathroom with a dark wood vanity, white basin and grey stone wall tiles"></div>
<div class="abs hero-caption">
  <h2>MORBI MOLLIS, ARCU VITAE</h2>
  <h3>DIGNISSIM PHARETRA ERO</h3>
  <p>Jerta baditaut onsequer untur magni dolores eoquie volup tate msequi nesciunt. Voluptatem accusantium dolorem.</p>
</div>
<div class="abs dots"><i></i><i></i><i></i><i></i></div>

<section class="abs welcome">
  <h1>Welcome to our Website</h1>
  <p>Claritas est etiam processus dynamicus, qui sequitur mutationem consuetudium lectorum. Mirum est notare quam littera gothica, quai minunc putamus parum claram, anteposuerit litterarum in the formas humanitatis per seacula quarta decima et quinta decima.</p>
</section>
<div class="abs btn">READ MORE</div>
<div class="abs divider"></div>

<div class="abs feature" style="left:54px">
  <div class="ring"><div class="disc">
    <svg width="52" height="52" viewBox="0 0 52 52" fill="none" stroke="#fff"><circle cx="20" cy="30" r="11" stroke-width="6" stroke-dasharray="4 3.2"/><circle cx="20" cy="30" r="5" stroke-width="3"/><circle cx="36" cy="15" r="7" stroke-width="4" stroke-dasharray="3 2.5"/></svg>
  </div></div>
  <h4>Services</h4>
  <p>Lorem ipsum dolor sit amet<br>ing elit.Morbi ut elipsum tristiqu<br>Pellentesque habitant morb</p>
</div>
<div class="abs feature" style="left:249px">
  <div class="ring"><div class="disc">
    <svg width="50" height="50" viewBox="0 0 50 50" fill="none" stroke="#fff" stroke-width="2.5" stroke-linejoin="round"><path d="M6 28 L44 8 L34 44 L24 32 Z"/><path d="M44 8 L24 32 L22 42"/></svg>
  </div></div>
  <h4>How to Order?</h4>
  <p>Lorem ipsum dolor sit amet<br>ing elit.Morbi ut elipsum tristiqu<br>Pellentesque habitant morb</p>
</div>
<div class="abs feature" style="left:442px">
  <div class="ring"><div class="disc">
    <svg width="60" height="50" viewBox="0 0 60 50"><rect x="8" y="14" width="28" height="22" rx="2" fill="#fff"/><path d="M37 20h10l7 9v7H37z" fill="#fff"/><circle cx="17" cy="38" r="5" fill="#fff" stroke="#1e1e1e" stroke-width="2"/><circle cx="46" cy="38" r="5" fill="#fff" stroke="#1e1e1e" stroke-width="2"/><circle cx="13" cy="14" r="9" fill="#1e1e1e" stroke="#fff" stroke-width="2.5"/><path d="M13 9v5h4" stroke="#fff" stroke-width="2" fill="none"/></svg>
  </div></div>
  <h4>Delivery</h4>
  <p>Lorem ipsum dolor sit amet<br>ing elit.Morbi ut elipsum tristiqu<br>Pellentesque habitant morb</p>
</div>
<div class="abs feature" style="left:636px">
  <div class="ring"><div class="disc">
    <svg width="56" height="46" viewBox="0 0 56 46" fill="none" stroke="#fff" stroke-width="2.5" stroke-linejoin="round"><path d="M28 4 L52 16 L28 28 L4 16 Z" fill="#fff"/><path d="M4 23 L28 35 L52 23"/><path d="M4 30 L28 42 L52 30"/></svg>
  </div></div>
  <h4>Finishing</h4>
  <p>Lorem ipsum dolor sit amet<br>ing elit.Morbi ut elipsum tristiqu<br>Pellentesque habitant morb</p>
</div>

<section class="abs projects">
  <h2>Latest Projects</h2>
  <div class="abs project" style="left:62px;width:222px">
    <div class="photo" role="img" aria-label="Office interior with dark desk, chairs and framed print on a stone wall" style="background:linear-gradient(90deg,#8c7e6a,#b9b1a3 45%,#5a5550 70%,#e8e8e8)"></div>
    <p>Lorem ipsum dolor sit amet, consectetur adipisicin g elit, sed do eiusmod tempor.</p>
  </div>
  <div class="abs project" style="left:326px;width:218px">
    <div class="photo" role="img" aria-label="Bathroom with dark slate floor tiles and a white basin" style="background:linear-gradient(135deg,#2c3b40,#4b5a5f 50%,#cfcfcf 80%,#3a4448)"></div>
    <p>Lorem ipsum dolor sit amet, consectetur adipisicin g elit, sed do eiusmod tempor.</p>
  </div>
  <div class="abs project" style="left:589px;width:218px">
    <div class="photo" role="img" aria-label="Bright white interior ceiling with a round light fitting" style="background:linear-gradient(90deg,#d8d4d0,#f2f0ec 45%,#e0ddd9 75%,#cfcac5)"></div>
    <p>Lorem ipsum dolor sit amet, consectetur adipisicin g elit, sed do eiusmod tempor.</p>
  </div>
</section>

<footer class="abs footer">
  <div class="abs col" style="left:63px"><h5>FeedbacK Portal</h5><ul><li>Team Portal</li><li>FeedbacK Exchange</li><li>Proin sit amet nulla</li><li>Consectetur adipiscing</li><li>Malesuada ullamcor</li></ul></div>
  <div class="abs col" style="left:223px"><h5>Who We Are</h5><ul><li>About us</li><li>Eoidem temper</li><li>Consectetur adiping</li><li>Sed id purus vel</li><li>Lorem ipsum</li></ul></div>
  <div class="abs col" style="left:363px"><h5>Outreach</h5><ul><li>Sed scelerisque</li><li>Consectetur adipisicing</li><li>FeedbacK Attends</li><li>Venture eoim2013</li><li>Ready to Tee Up First of Three</li></ul></div>
  <div class="abs col" style="left:542px"><h5>Links</h5><ul><li>About us</li><li>Consectetur adicing</li><li>Consectetur adicing</li><li>Sed id purus vel</li><li>Lorem ipsum</li></ul></div>
  <div class="abs col" style="left:693px"><h5>Other Information</h5><ul><li>Privacy Policy</li><li>Terms &amp; Conditions</li></ul></div>
  <div class="abs foot-brand">Copper Ridge<br>Marmora</div>
</footer>

<div class="abs bottom">
  <p>Copyrights 2013. All Rights Reserved.</p>
  <span class="social" style="left:658px"></span>
  <span class="social" style="left:693px;background:#555"></span>
  <span class="social" style="left:728px"></span>
  <span class="social" style="left:762px"></span>
</div>

</body>
</html>
```